Business Card Design

New business card design

Target Market(s)

Residential & Commercial Property Managers

Industry/Entity Type

Plumbing Services

Contact Information for Business Card

Name - Rowan Keddle, title - Director, Phone Number - 0431 286 517, email - rowan@tbk-plumbing.com.au, Company ABN - 73 215 904 386,

Font styles to use
Sans Serif

Colors
0054AA
0677BA
7BADD7
CADEEF
E8F1F8

```html
<!DOCTYPE html>
<html lang="en">
<head>
<meta charset="utf-8">
<title>TBK Plumbing – Business Card</title>
<link rel="stylesheet" href="https://fonts.googleapis.com/css2?family=Roboto:wght@300;400;500;700&display=swap">
<style>
  :root {
    --bg: #d9dcdf;
    --card-dark: #1c1d1f;
    --card-light: #f4f4f2;
    --ink: #1c1d1f;
    --muted: #8a8a88;
    --accent: #1ca0e0;
    --logo-light: #f2f2f2;
    --band-text: #e9e9e9;
  }
  * { box-sizing: border-box; margin: 0; padding: 0; }
  html, body { width: 1200px; height: 852px; overflow: hidden; }
  body {
    background: var(--bg);
    font-family: "Roboto", Arial, sans-serif;
    position: relative;
  }
  .card {
    position: absolute;
    top: 276px;
    width: 520px;
    height: 300px;
    border-radius: 22px;
    overflow: hidden;
    box-shadow: 0 0 0 3px var(--accent);
  }
  .card--front { left: 50px; background: var(--card-dark); }
  .card--back  { left: 630px; background: var(--card-light); }

  .brand {
    display: flex;
    align-items: center;
    gap: 10px;
    font-weight: 300;
    letter-spacing: 2px;
    white-space: nowrap;
  }
  .brand__dot {
    border-radius: 50%;
    background: var(--accent);
    flex: none;
  }
  .card--front .brand {
    position: absolute;
    left: 0; right: 0; top: 110px;
    justify-content: center;
    color: var(--logo-light);
    font-size: 58px;
  }
  .card--front .brand__dot { width: 16px; height: 16px; }

  .card--back .brand {
    position: absolute;
    left: 30px; top: 44px;
    color: var(--ink);
    font-size: 34px;
    letter-spacing: 1.5px;
  }
  .card--back .brand__dot { width: 11px; height: 11px; }

  .contacts {
    position: absolute;
    left: 300px; top: 36px;
    list-style: none;
    font-size: 12.5px;
    color: var(--ink);
    line-height: 20px;
    white-space: nowrap;
  }
  .contacts li { display: flex; align-items: center; gap: 8px; }
  .contacts svg { width: 12px; height: 12px; fill: var(--accent); flex: none; }

  .person { position: absolute; left: 30px; top: 168px; }
  .person__name { font-size: 20px; font-weight: 700; color: var(--ink); }
  .person__title { font-size: 12.5px; color: var(--muted); margin-top: 2px; }
  .address {
    position: absolute; left: 30px; top: 238px;
    font-size: 12.5px; line-height: 18px; color: var(--ink);
  }

  .company-band {
    position: absolute;
    right: 0; bottom: 0;
    width: 240px; height: 52px;
    background: var(--card-dark);
    clip-path: polygon(18px 0, 100% 0, 100% 100%, 0 100%);
    display: flex; align-items: center; justify-content: center;
    padding-left: 18px;
    color: var(--band-text);
    font-size: 12px;
  }
  .company-band__accent {
    position: absolute;
    right: 222px; bottom: 0;
    width: 34px; height: 52px;
    background: var(--accent);
    clip-path: polygon(18px 0, 100% 0, 16px 100%, 0 100%);
  }
</style>
</head>
<body>
  <section class="card card--front" aria-label="Card front">
    <div class="brand"><span class="brand__dot"></span>TBK Plumbing</div>
  </section>

  <section class="card card--back" aria-label="Card back">
    <div class="brand"><span class="brand__dot"></span>TBK Plumbing</div>

    <ul class="contacts">
      <li>
        <svg viewBox="0 0 24 24" aria-hidden="true"><path d="M6.6 10.8a15 15 0 0 0 6.6 6.6l2.2-2.2a1 1 0 0 1 1-.25 11.4 11.4 0 0 0 3.6.57 1 1 0 0 1 1 1V20a1 1 0 0 1-1 1A17 17 0 0 1 3 4a1 1 0 0 1 1-1h3.5a1 1 0 0 1 1 1c0 1.25.2 2.45.57 3.57a1 1 0 0 1-.25 1z"/></svg>
        0431 286 517
      </li>
      <li>
        <svg viewBox="0 0 24 24" aria-hidden="true"><path d="M2 5h20v14H2zm2 2v.5l8 5 8-5V7l-8 5z"/></svg>
        rowan@tbk-plumbing.com.au
      </li>
      <li>
        <svg viewBox="0 0 24 24" aria-hidden="true"><circle cx="12" cy="12" r="10"/></svg>
        www.tbk-plumbing.com.au
      </li>
      <li>
        <svg viewBox="0 0 24 24" aria-hidden="true"><rect x="3" y="3" width="18" height="18" rx="2"/></svg>
        ABN 73 215 904 386
      </li>
    </ul>

    <div class="person">
      <p class="person__name">Rowan Keddle</p>
      <p class="person__title">Director</p>
    </div>

    <p class="address">17 Harbour Rd, Marlow Bay,<br>NSW 2289</p>

    <div class="company-band__accent"></div>
    <div class="company-band">TBK Plumbing Services Pty Ltd</div>
  </section>
</body>
</html>
```